Drug Testing Kit needs a packaging design

I need a professional yet eye catching design for my 5 in 1 drug testing kit.

We call ourselves Coastal Assay Laboratories or "CAL" and am currently running an Ebay business selling Drug Testing Kits. Based in Australia, I am now looking to market my products to local chemists and brach out to the commercial market.

We currently sell a number of different diagnostic tests;Single purchase tests are; THC (Marijuana), Opiates, Amphetamines. We also sell "3 in 1" tests (THC, Amphetamines, MDMA and we sell "5 in 1" tests (THC, COCAINE, Amphetamines, MDMA and Opiates.

I would like to use design that integrates the colours of the individually wrapped items and catches the eye of the customer. I want to market the product to look very professional, almost like it's a medication.
Updates

Measurement changed from ng/ml to μg/L

email to feature on rear 

info@coastalassaylabsonline.com

Target Market(s)

This product will be marketed to Pharmacies and Chemists (Drug Stores) for sale to the general public.

Industry/Entity Type

Business

Requirements
Must have
• Must feature the CAL logo (which is just CAL in font type) somewhere on the packaging.

Must have the Cutoff Limits of the drugs listed for the 5 in 1 test. (THC 50μg/L, COCAINE 300μg/L, AMPHETAMINES 1000μg/L, OPIATES 300μg/L, MDMA 500μg/L(Ecstasy).

The CE approval of the item must be included somewhere on the packaging. ISO13485 ISO9001 ISO14001

Contents 1x Multi Panel Urine Drug Testing Kit, 1x Instruction manual

Email on rear
Nice to have
• The proper chemical names on the front.

'Urine drug tests screen the urine for the presence of a parent drug or its metabolites. Urine is generally considered the best medium to measure in terms of detecting drugs and drug metabolites. Compared to blood, urine offers a longer window of detection that may be one to three days for some drugs and up to 30 days for others. Urine drug testing is by far the most extensively studied and validated process for drug testing. A non-negative (positive) result indicates that the amount of drug / metabolites are above the cutoff limits for the test. '
Should not have
• Nothing unprofessional or suggesting that drug use is bad or not ok. We are not marketing that drug use is illegal or bad. We do not want potential customers to feel guilty when purchasing our items.

```html
<!DOCTYPE html>
<html lang="en">
<head>
<meta charset="utf-8">
<title>CAL 5 in 1 Drug Testing Kit – Packaging Net</title>
<link rel="stylesheet" href="https://fonts.googleapis.com/css2?family=Arimo:wght@400;700&family=Open+Sans:wght@600;800&display=swap">
<style>
  :root {
    --bg-light: #8ff3f6;
    --bg-mid: #55e6ef;
    --flap: #00ccff;
    --panel-blue: #3fd0ff;
    --deep-blue: #0a1fd0;
    --title-black: #111111;
    --white: #ffffff;
    --rule: #c9a24a;
    --brand-cyan: #22e0e6;
    --edge: rgba(255,255,255,0.55);
  }
  * { box-sizing: border-box; margin: 0; padding: 0; }
  html, body { width: 1200px; height: 1000px; overflow: hidden; }
  body { font-family: "Arimo", Arial, sans-serif; }

  .stage {
    position: relative; width: 1200px; height: 1000px; overflow: hidden;
    background:
      radial-gradient(ellipse 520px 380px at 20% 12%, rgba(255,255,255,0.45), transparent 70%),
      radial-gradient(ellipse 600px 420px at 85% 80%, rgba(255,255,255,0.35), transparent 70%),
      linear-gradient(135deg, var(--bg-mid), var(--bg-light) 45%, var(--bg-mid));
  }
  .part { position: absolute; }
  .flap { background: var(--flap); border: 1px solid var(--edge); }

  /* product count label: plain text, one size, one weight */
  .count-label {
    display: inline-block; background: var(--white); color: var(--deep-blue);
    font-family: "Open Sans", sans-serif; font-weight: 800; line-height: 1;
    white-space: nowrap;
  }
  .flap-title { font-family: "Open Sans", sans-serif; font-weight: 800; color: var(--white); font-size: 25px; white-space: nowrap; }

  /* top flap of front face */
  .top-flap-outer { left: 108px; top: 53px; width: 449px; height: 45px; }
  .top-flap-inner { left: 108px; top: 97px; width: 449px; height: 66px;
    display: flex; align-items: center; justify-content: center; }
  .upside { transform: rotate(180deg); display: flex; align-items: center; gap: 22px; }
  .upside .count-label { font-size: 28px; padding: 8px 12px; }

  /* front face */
  .front-strip { left: 77px; top: 163px; width: 31px; height: 545px; background: var(--flap); }
  .front-face { left: 108px; top: 163px; width: 449px; height: 545px;
    background:
      radial-gradient(ellipse 260px 300px at 92% 30%, rgba(80,200,255,0.55), transparent 70%),
      radial-gradient(ellipse 220px 140px at 40% 90%, rgba(70,190,255,0.7), transparent 70%),
      radial-gradient(ellipse 200px 200px at 10% 10%, rgba(120,215,255,0.5), transparent 70%),
      var(--white); }
  .base-band { background: var(--white); border-top: 3px solid var(--rule); }
  .front-band { left: 77px; top: 708px; width: 480px; height: 110px; }

  .cert-line { left: 338px; top: 187px; display: flex; align-items: center; gap: 6px;
    font-weight: 700; font-size: 12px; color: var(--title-black); }
  .cert-mark { width: 12px; height: 10px; background: var(--title-black); }

  .title-block { display: flex; flex-direction: column; }
  .title-block .count-label { background: transparent; font-size: 44px; line-height: 52px; }
  .kit-title { font-family: "Open Sans", sans-serif; font-weight: 800; font-size: 35px;
    line-height: 44px; letter-spacing: 0.3px; white-space: nowrap; }
  .front-title { left: 163px; top: 233px; }
  .front-title .kit-title { color: var(--title-black); text-shadow: 2px 2px 0 rgba(255,255,255,0.9); }
  .back-title { left: 682px; top: 233px; }
  .back-title .kit-title { color: var(--white); text-shadow: 2px 2px 2px rgba(0,0,0,0.45); }

  .drug-list { list-style: none; font-weight: 700; font-size: 17px; line-height: 21px; }
  .drug-list li::before { content: "• "; color: var(--white); }
  .front-list { left: 163px; top: 353px; color: var(--title-black); }
  .back-list { left: 681px; top: 353px; color: var(--white); text-shadow: 1px 1px 1px rgba(0,0,0,0.35); }

  .contents { left: 164px; top: 635px; font-size: 14px; line-height: 18px; color: var(--title-black); }

  .brand { font-weight: 700; font-size: 33px; color: var(--brand-cyan); letter-spacing: 1px; }
  .front-brand { left: 130px; top: 750px; }
  .back-brand { left: 663px; top: 750px; }

  /* side panel */
  .side-top { left: 557px; top: 108px; width: 70px; height: 55px; }
  .side-panel { left: 557px; top: 163px; width: 70px; height: 655px; background: var(--flap); }
  .side-title { position: absolute; left: 35px; top: 248px; transform: translate(-50%,-50%) rotate(-90deg);
    white-space: nowrap; font-family: "Open Sans", sans-serif; font-weight: 800; color: var(--white);
    font-size: 33px; letter-spacing: 2.5px; }
  .side-badge { position: absolute; left: 1px; top: 447px; width: 68px; height: 110px;
    background: var(--white); display: flex; align-items: center; justify-content: center; }
  .side-badge .count-label { transform: rotate(-90deg); font-size: 30px; }

  /* back face */
  .back-face { left: 627px; top: 163px; width: 449px; height: 545px;
    background:
      radial-gradient(ellipse 200px 300px at 75% 55%, rgba(255,255,255,0.75), transparent 70%),
      radial-gradient(ellipse 160px 220px at 5% 5%, rgba(255,255,255,0.7), transparent 70%),
      var(--panel-blue); }
  .back-band { left: 627px; top: 708px; width: 449px; height: 110px; }

  .cutoff { left: 681px; top: 565px; color: var(--white); font-size: 11.5px; line-height: 14px; }
  .cutoff h3 { font-weight: 400; font-size: 12px; border-bottom: 1.5px solid var(--white);
    width: 168px; padding-bottom: 1px; margin-bottom: 9px; }

  /* right side strip */
  .right-top { left: 1076px; top: 108px; width: 67px; height: 55px; }
  .right-panel { left: 1076px; top: 163px; width: 67px; height: 655px; background: var(--flap); }
  .right-badge { position: absolute; left: 1px; top: 77px; width: 65px; height: 135px; background: var(--white);
    display: flex; align-items: center; justify-content: center; }
  .right-badge .count-label { transform: rotate(90deg); font-size: 30px; }
  .right-title { position: absolute; left: 33px; top: 412px; transform: translate(-50%,-50%) rotate(90deg);
    white-space: nowrap; font-family: "Open Sans", sans-serif; font-weight: 800; color: var(--white);
    font-size: 33px; letter-spacing: 2.5px; }

  /* bottom flap of back face */
  .bottom-flap { left: 627px; top: 818px; width: 449px; height: 112px; }
  .bottom-flap-line { position: absolute; left: 0; right: 0; top: 68px; border-top: 1px solid var(--edge); }
  .bottom-flap-label { position: absolute; left: 48px; top: 12px; display: flex; align-items: center; gap: 20px; }
  .bottom-flap-label .count-label { font-size: 28px; padding: 8px 12px; }

  .net-label { left: 178px; top: 893px; font-family: "Open Sans", sans-serif; font-weight: 600;
    font-size: 46px; color: var(--white); }
</style>
</head>
<body>
<main class="stage">

  <!-- front face flaps -->
  <div class="part flap top-flap-outer"></div>
  <div class="part flap top-flap-inner">
    <div class="upside">
      <span class="count-label">5 in 1</span>
      <span class="flap-title">Drug Testing Kit</span>
    </div>
  </div>

  <!-- front face -->
  <div class="part front-strip"></div>
  <div class="part front-face"></div>
  <div class="part base-band front-band"></div>

  <div class="part cert-line"><span class="cert-mark"></span>ISO13485 ISO9001 ISO14001</div>

  <div class="part title-block front-title">
    <span class="count-label">5 in 1</span>
    <h1 class="kit-title">Drug Testing Kit</h1>
  </div>

  <ul class="part drug-list front-list">
    <li>AMPHETAMINES</li>
    <li>COCAINE</li>
    <li>MARIJUANA (THC)</li>
    <li>OPIATES</li>
    <li>MDMA</li>
  </ul>

  <div class="part contents">
    <p>Contents</p>
    <p>1x 5 in 1 Urine Drug Testing Kit</p>
    <p>1x instruction manual</p>
  </div>

  <div class="part brand front-brand">CAL</div>

  <!-- side panel -->
  <div class="part flap side-top"></div>
  <div class="part side-panel">
    <span class="side-title">Drug Testing Kit</span>
    <div class="side-badge"><span class="count-label">5 in 1</span></div>
  </div>

  <!-- back face -->
  <div class="part back-face"></div>
  <div class="part base-band back-band"></div>

  <div class="part title-block back-title">
    <span class="count-label">5 in 1</span>
    <h2 class="kit-title">Drug Testing Kit</h2>
  </div>

  <ul class="part drug-list back-list">
    <li>SPEED, ICE, CRYSTAL</li>
    <li>COKE, CHARLIE</li>
    <li>CANNABIS, POT, GRASS</li>
    <li>HEROIN</li>
    <li>MORPHINE</li>
  </ul>

  <div class="part cutoff">
    <h3>Cutoff Limits of the drugs</h3>
    <p>THC : 50ng/ml</p>
    <p>COCAINE : 300ng/ml</p>
    <p>AMPHETAMINES : 1000ng/ml</p>
    <p>OPIATES : 300ng/ml</p>
    <p>MDMA : 500ng/ml (Ecstasy)</p>
  </div>

  <div class="part brand back-brand">CAL</div>

  <!-- right side strip -->
  <div class="part flap right-top"></div>
  <div class="part right-panel">
    <div class="right-badge"><span class="count-label">5 in 1</span></div>
    <span class="right-title">Drug Testing Kit</span>
  </div>

  <!-- bottom flap -->
  <div class="part flap bottom-flap">
    <div class="bottom-flap-label">
      <span class="count-label">5 in 1</span>
      <span class="flap-title">Drug Testing Kit</span>
    </div>
    <div class="bottom-flap-line"></div>
  </div>

  <div class="part net-label">Full View</div>
</main>
</body>
</html>
```